VELORA Brisbane Tiling Service

My name is Milos Brendt i need a business card for a new company. We are wall and floor tilers based in Brisbane, our company is Velorix Brisbane Tiling Service.
We would like a logo from our website used on our cards. Our website is www.velorix.com.au

I would like my Chatterbook and Postwave accounts on my card.

Industry/Entity Type

Business

Colors
0692cd
3176b5
33a6d7
85cae6

```html
<!DOCTYPE html>
<html lang="en">
<head>
<meta charset="utf-8">
<title>Velorix Brisbane Tiling Service – Business Card</title>
<link rel="stylesheet" href="https://fonts.googleapis.com/css2?family=Lato:wght@300;400;700;900&display=swap">
<style>
  :root{
    --blue:#0692cd;
    --blue-deep:#3176b5;
    --blue-mid:#33a6d7;
    --blue-soft:#85cae6;
    --ink:#3d3d3d;
    --ink-soft:#5a5a5a;
    --card:#f4f4f4;
    --card-edge:#e6e6e6;
    --stage:#2b2b2b;
  }
  *{margin:0;padding:0;box-sizing:border-box}
  html,body{width:1200px;height:997px;overflow:hidden}
  body{background:var(--stage);font-family:"Lato",sans-serif;position:relative}

  .card{
    position:absolute;width:600px;height:343px;border-radius:22px;
    background:linear-gradient(160deg,#ffffff 0%,var(--card) 60%,var(--card-edge) 100%);
    overflow:hidden;
  }
  .card--back{left:90px;top:110px}
  .card--front{left:510px;top:545px}

  /* back side */
  .estimate{position:absolute;left:50px;top:46px}
  .estimate__label{font-weight:900;font-size:26px;color:var(--ink);letter-spacing:.5px}
  .estimate__phone{font-weight:900;font-size:44px;color:var(--blue);letter-spacing:1px;line-height:1.1}

  .brand{position:absolute;display:flex;align-items:center}
  .brand__mark{background:var(--blue-deep);flex:none}
  .brand__name{color:var(--blue);font-weight:400;line-height:1}
  .brand__tagline{color:var(--ink-soft);font-weight:400;line-height:1.1}

  .card--back .brand{left:50px;top:180px}
  .card--back .brand__mark{width:118px;height:118px;margin-right:22px}
  .card--back .brand__name{font-size:72px}
  .card--back .brand__tagline{font-size:30px}

  /* front side */
  .brand-plate{position:absolute;right:22px;top:26px;background:#e3e3e3;padding:10px 16px 10px 12px}
  .card--front .brand{position:static}
  .card--front .brand__mark{width:60px;height:60px;margin-right:12px}
  .card--front .brand__name{font-size:38px}
  .card--front .brand__tagline{font-size:16px}

  .rule{position:absolute;left:300px;top:128px;width:270px;height:2px;background:var(--blue-deep)}
  .rule--long{left:280px;top:190px;width:0}

  .person{position:absolute;left:40px;top:175px}
  .person__name{font-weight:700;font-size:24px;color:var(--blue-deep)}
  .person__title{font-size:17px;color:var(--ink-soft);margin-top:2px}
  .person__line{position:absolute;left:210px;top:178px;width:150px;height:2px;background:var(--blue-deep)}

  .contacts{position:absolute;left:40px;top:246px;list-style:none}
  .contacts li{display:flex;align-items:center;font-size:15px;color:var(--ink);margin-bottom:11px}
  .contacts svg{width:20px;height:20px;margin-right:14px;flex:none}

  .social{position:absolute;left:370px;top:150px;list-style:none}
  .social li{display:flex;align-items:center;font-size:14px;color:var(--ink);margin-bottom:12px}
  .social__dot{width:12px;height:12px;border-radius:50%;background:var(--blue-deep);margin-right:12px;flex:none}
  .social__abn{color:var(--blue-deep);font-weight:700;margin-top:4px}
</style>
</head>
<body>

<section class="card card--back" aria-label="Card back">
  <div class="estimate">
    <p class="estimate__label">CALL FOR A FREE ESTIMATE</p>
    <p class="estimate__phone">0400 555 019</p>
  </div>
  <div class="brand">
    <div class="brand__mark"></div>
    <div>
      <p class="brand__name">velorix</p>
      <p class="brand__tagline">brisbane tiling service</p>
    </div>
  </div>
</section>

<section class="card card--front" aria-label="Card front">
  <div class="brand-plate">
    <div class="brand">
      <div class="brand__mark"></div>
      <div>
        <p class="brand__name">velorix</p>
        <p class="brand__tagline">brisbane tiling service</p>
      </div>
    </div>
  </div>
  <div class="rule"></div>

  <div class="person">
    <p class="person__name">Milos Brendt</p>
    <p class="person__title">Construction Manager</p>
  </div>
  <div class="person__line"></div>

  <ul class="contacts">
    <li>
      <svg viewBox="0 0 20 20" aria-hidden="true"><rect x="5" y="1.5" width="10" height="17" rx="2" fill="none" stroke="#3176b5" stroke-width="2"/><circle cx="10" cy="15.3" r="1" fill="#3176b5"/></svg>
      07 3555 0142
    </li>
    <li>
      <svg viewBox="0 0 20 20" aria-hidden="true"><rect x="1.5" y="4" width="17" height="12" fill="#3176b5"/><path d="M1.5 4 L10 11 L18.5 4" fill="none" stroke="#fff" stroke-width="1.5"/></svg>
      info@velorix.com.au
    </li>
    <li>
      <svg viewBox="0 0 20 20" aria-hidden="true"><g fill="none" stroke="#3176b5" stroke-width="2.2" stroke-linecap="round"><path d="M8.5 11.5 L11.5 8.5"/><path d="M9 6 L11 4 a3.2 3.2 0 0 1 4.5 4.5 L13.5 10.5"/><path d="M11 14 L9 16 a3.2 3.2 0 0 1 -4.5 -4.5 L6.5 9.5"/></g></svg>
      www.velorix.com.au
    </li>
  </ul>

  <ul class="social">
    <li><span class="social__dot"></span>postwave.com/Infovelorix</li>
    <li><span class="social__dot"></span>chatterbook.com/Velorix-Brisbane</li>
    <li class="social__abn">Abn: 51824736019</li>
  </ul>
</section>

</body>
</html>
```